Marlow Estate Fixers (Handyman / Home Improvement Company)

Looking for a double sided professional looking business card with Logo attached to be highlighted on one side and throwing in an image of a handyman as an option would be nice to see as well. We are a company focused on providing quality Handyman and Home improvement services in a timely manner that is done right the first time with integrity

Industry/Entity Type

Handyman / Home Improvement

Contact Information for Business Card

(LOGO, Name, Mobile and office phone numbers, email) on front side of card, (the words "The SOLUTION to all of your Handyman and Home Improvement needs" followed by "Family Owned and Operated" at the very bottom) on the back.

Colors
EB3D1F
EC4F4E
F09395
F8D3D4
FCEDEE

Requirements
Must have
• Red, Gray, Black Color scheme
Should not have
• No Yellow or Blue colors

```html
<!DOCTYPE html>
<html lang="en">
<head>
<meta charset="utf-8">
<title>Marlow Estate Fixers – Business Card</title>
<link href="https://fonts.googleapis.com/css2?family=Anton&family=Montserrat:wght@400;500;700;800&display=swap" rel="stylesheet">
<style>
  :root {
    --bg: #1b1b1b;
    --red: #e62a2f;
    --red-dark: #b81f24;
    --ink: #111111;
    --gray: #3a3a3a;
    --text: #1f1f1f;
    --white: #ffffff;
    --card-radius: 20px;
  }
  * { margin: 0; padding: 0; box-sizing: border-box; }
  html, body { width: 1200px; height: 1059px; overflow: hidden; background: var(--bg); }
  .stage { position: relative; width: 1200px; height: 1059px; }

  .card { position: absolute; left: 261px; width: 716px; border-radius: var(--card-radius); overflow: hidden; }

  /* Front */
  .card-front { top: 95px; height: 408px; background: var(--white); }
  .brand { position: absolute; left: 90px; top: 158px; width: 250px; display: flex; align-items: center; gap: 14px; }
  .brand-dot { flex: none; width: 38px; height: 38px; border-radius: 50%; background: var(--red); }
  .brand-name { font-family: 'Montserrat', sans-serif; font-weight: 800; font-size: 26px; line-height: 1.1; color: var(--ink); text-transform: uppercase; }
  .divider { position: absolute; left: 352px; top: 120px; width: 2px; height: 170px; background: var(--red); }
  .contact { position: absolute; left: 382px; top: 118px; font-family: 'Montserrat', sans-serif; }
  .contact-name { font-weight: 700; font-size: 28px; color: var(--red); line-height: 1; }
  .contact-role { font-weight: 400; font-size: 19px; color: var(--text); margin-top: 10px; }
  .contact-list { list-style: none; margin-top: 18px; }
  .contact-list li { display: flex; align-items: center; gap: 13px; font-size: 19.5px; color: var(--text); height: 32px; }
  .contact-list svg { width: 20px; height: 20px; fill: var(--red); flex: none; }
  .front-band { position: absolute; left: 0; bottom: 0; width: 100%; height: 12px; }

  /* Back */
  .card-back { top: 529px; height: 410px; background: var(--red); color: var(--white); }
  .tagline { position: absolute; left: 20px; top: 92px; width: 400px; text-align: center; }
  .tagline-lead { font-family: 'Montserrat', sans-serif; font-weight: 700; font-size: 28.5px; line-height: 1.2; white-space: nowrap; }
  .tagline-main { font-family: 'Anton', sans-serif; font-size: 42px; line-height: 1.35; white-space: nowrap; }
  .motto { position: absolute; left: 20px; top: 357px; width: 400px; text-align: center; font-family: 'Montserrat', sans-serif; font-weight: 700; font-size: 22.5px; }
  .handyman-art { position: absolute; left: 415px; top: 18px; width: 296px; height: 382px; border-radius: 14px;
    background: radial-gradient(ellipse at 50% 45%, #f0585c 0%, var(--red-dark) 100%); }
</style>
</head>
<body>
<div class="stage">

  <section class="card card-front">
    <div class="brand">
      <span class="brand-dot"></span>
      <span class="brand-name">Marlow Estate Fixers</span>
    </div>
    <div class="divider"></div>
    <div class="contact">
      <p class="contact-name">Daniel Hargrove</p>
      <p class="contact-role">Owner</p>
      <ul class="contact-list">
        <li><svg viewBox="0 0 24 24"><path d="M7 1h10a2 2 0 0 1 2 2v18a2 2 0 0 1-2 2H7a2 2 0 0 1-2-2V3a2 2 0 0 1 2-2zm0 3v14h10V4H7zm5 15.5a1 1 0 1 0 0 2 1 1 0 0 0 0-2z"/></svg>044-987 650 321</li>
        <li><svg viewBox="0 0 24 24"><path d="M2 9c0-3 4-5 10-5s10 2 10 5v2h-5V8.5c-1.5-.6-3-.8-5-.8s-3.5.2-5 .8V11H2V9zm4 3h12l2 9H4l2-9zm6 2a3 3 0 1 0 0 6 3 3 0 0 0 0-6z"/></svg>044-987 650 322</li>
        <li><svg viewBox="0 0 24 24"><path d="M2 5h20v14H2V5zm2 2v.5l8 5 8-5V7H4z"/></svg>info@marlowfixers.com</li>
      </ul>
    </div>
    <svg class="front-band" viewBox="0 0 716 12" preserveAspectRatio="none">
      <polygon points="0,0 352,0 358,12 0,12" fill="var(--red)"/>
      <polygon points="358,0 716,0 716,12 366,12" fill="var(--gray)"/>
    </svg>
  </section>

  <section class="card card-back">
    <div class="tagline">
      <p class="tagline-lead">Your SOLUTION to all of</p>
      <p class="tagline-main">your Handyman and</p>
      <p class="tagline-main">Home Improvement</p>
      <p class="tagline-main">Needs</p>
    </div>
    <p class="motto">Family Owned and Operated</p>
    <div class="handyman-art" role="img" aria-label="Illustration of a cheerful handyman in work overalls holding a pipe wrench and spanner"></div>
  </section>

</div>
</body>
</html>
```